Corvane Systems Web Site

Need a complete redesign of the website to make it cleaner and up to date.
Current website: http://www.corvanesystems.example/
I am looking for a single page design focused on giving all the information about the POC (Pump Off Controller). And highlighting its benefits: Increased oil production, quick ROI, ease of use and low maintenance cost.
Here's a presentation of the product:
http://slidewharf.example/qk4mtz8vn2ra/?utm_campaign=share&utm_medium=copy&rc=ex0share
Please consider participating on the flyer design:
http://jobs.artmarket.example/job.aspx?id=391726
Here are some design examples of web sites I like:
http://www.bright-harbor.example/
I just added the source files for our business cards. I would like to see designs that incorporate the "tag cloud" on the back of the card..
Target Market(s)
Oil field decision makers. Engineers and technicians from 20 to 60.
Investors and venture capitalists.
Industry/Entity Type
Cleaner
Requirements
Must have
- Single page design
Nice to have
- Responsive web design

```html
<!DOCTYPE html>
<html lang="en">
<head>
<meta charset="utf-8">
<title>Corvane Systems</title>
<link rel="stylesheet" href="https://fonts.googleapis.com/css2?family=Lato:ital,wght@0,400;0,700;0,900;1,400&family=Roboto+Condensed:ital,wght@1,700&display=swap">
<style>
:root{
  --navy:#0c1a63;
  --navy-dark:#08124a;
  --red:#d7262b;
  --red-dark:#8e1417;
  --ink:#333333;
  --muted:#666666;
  --light:#ececec;
  --line:#cfcfcf;
  --footer:#2c2c2c;
  --white:#ffffff;
}
*{box-sizing:border-box;margin:0;padding:0}
html,body{width:1200px;height:2567px;overflow:hidden;background:var(--white)}
body{font-family:'Lato',sans-serif;color:var(--ink)}
.page{position:relative;width:1200px;height:2567px}
.abs{position:absolute}

.topbar{left:0;top:0;width:1200px;height:34px;background:var(--navy)}
.topbar .phone{left:139px;top:6px;color:var(--white);font-weight:700;font-size:19px;display:flex;align-items:center;gap:8px}
.topbar .login{right:139px;top:8px;color:var(--white);font-weight:700;font-size:15px;display:flex;align-items:center;gap:7px}

.brand{left:139px;top:62px;display:flex;align-items:center;gap:10px;font-weight:900;font-size:30px;color:var(--navy)}
.brand .dot{width:30px;height:30px;border-radius:50%;background:var(--red)}
.nav{left:426px;top:86px;width:635px;height:44px;background:var(--navy);border-radius:4px;display:flex;justify-content:space-around;align-items:center}
.nav a{color:var(--white);text-decoration:none;font-weight:700;font-size:15px;position:relative;padding:12px 6px}
.nav a.active::before{content:"";position:absolute;left:0;right:0;top:-2px;height:4px;background:var(--red)}

.hero{left:0;top:150px;width:1200px;height:475px;background:linear-gradient(180deg,#dcdcdc 0%,#8a8a8a 35%,#3d3d3d 75%,#1e1e1e 100%)}
.hero .arrow{top:198px;width:36px;height:36px;border-radius:50%;background:rgba(255,255,255,.75)}
.hero .caption{left:0;bottom:0;width:1200px;height:52px;background:rgba(0,0,0,.55);color:var(--white);font-family:'Roboto Condensed',sans-serif;font-style:italic;font-weight:700;font-size:31px;text-align:center;line-height:52px}

.welcome h1{left:0;top:653px;width:1200px;text-align:center;font-size:44px;font-weight:700;color:#3a3a3a}
.welcome h1 span{color:var(--navy)}
.welcome .rule{left:368px;top:712px;width:464px;height:3px;background:var(--navy)}
.welcome p{left:171px;width:858px;text-align:center;font-size:15px;line-height:23px;color:var(--ink)}

.benefits{left:0;top:935px;width:1200px;height:723px;background:var(--light)}
.benefits h2{left:0;top:22px;width:1200px;text-align:center;font-size:42px;font-weight:700;color:#3a3a3a}
.benefits h2 span{color:var(--navy)}
.benefits .rule{left:472px;top:78px;width:256px;height:3px;background:var(--navy)}
.benefit{width:240px;text-align:center;font-size:21px;font-weight:700;color:#3a3a3a;line-height:26px}
.benefit .icon{width:120px;height:120px;margin:0 auto 12px;border-radius:50%;background:var(--white);box-shadow:0 2px 6px rgba(0,0,0,.15);display:flex;align-items:center;justify-content:center}
.hub{left:510px;top:240px;width:200px;height:120px;display:flex;align-items:center;justify-content:center;gap:8px;font-weight:900;font-size:30px;color:var(--navy)}
.hub .dot{width:28px;height:28px;border-radius:50%;background:var(--red)}

.promo{left:0;top:1658px;width:1200px;height:250px;background:radial-gradient(ellipse at 40% 50%,#e0383c 0%,#b81d22 50%,var(--red-dark) 100%)}
.promo .line{left:145px;color:var(--white);font-family:'Roboto Condensed',sans-serif;font-style:italic;font-weight:700;font-size:34px;line-height:38px}
.promo .big{font-size:50px}
.badge{left:867px;top:21px;width:192px;height:192px;border-radius:50%;background:#3a3a3a;border:6px solid #d9d9d9;display:flex;align-items:center;justify-content:center;text-align:center;color:var(--white);font-family:'Roboto Condensed',sans-serif;font-style:italic;font-weight:700;font-size:32px;line-height:34px;transform:rotate(-10deg)}

.feedback h3{left:0;top:1955px;width:1200px;text-align:center;font-size:27px;font-weight:900;color:var(--navy)}
.feedback .rule{left:139px;top:1999px;width:922px;height:2px;background:var(--line)}
.quote{left:139px;top:2049px;width:802px;height:107px;background:#eeeeee;border-radius:4px;padding:14px 48px 0 40px;font-size:13px;font-style:italic;color:var(--muted);line-height:21px}
.quote .mark{left:12px;top:6px;font-size:40px;color:#bdbdbd;font-style:normal}
.avatar{left:928px;top:2047px;width:112px;height:112px;border-radius:50%;border:5px solid var(--white);background:linear-gradient(160deg,#cfd6dd,#8f9aa6);box-shadow:0 1px 4px rgba(0,0,0,.25)}
.author{right:160px;top:2172px;font-size:13px;font-style:italic;color:#444}
.dots{left:143px;top:2168px;display:flex;gap:7px}
.dots i{width:11px;height:11px;border-radius:50%;background:#9a9a9a}
.dots i:first-child{background:var(--navy)}
.clients{left:139px;top:2231px;width:922px;height:58px;border-top:2px solid var(--line);display:flex;justify-content:space-between;align-items:center;color:#555;font-size:18px;font-weight:700}

.footer{left:0;top:2310px;width:1200px;height:225px;background:var(--footer);color:#cfcfcf}
.footer h4{position:absolute;top:34px;font-size:17px;font-weight:400;color:var(--white)}
.footer .col-rule{position:absolute;top:60px;height:1px;background:#555}
.footer ul{position:absolute;list-style:none;font-size:13px;line-height:25px}
.footer ul.links li::before{content:"› ";color:#999}
.contact li{display:flex;gap:10px;align-items:flex-start;line-height:17px;margin-bottom:8px}
.map{left:644px;top:2381px;width:218px;height:111px;background:linear-gradient(135deg,#d9e6c9,#b7d3e8 60%,#e9e3d1);border:3px solid var(--white)}
.maplink{left:644px;top:2496px;font-size:11px;color:var(--red)}
.foot-brand{left:909px;top:2400px;width:150px;text-align:center;color:#6d6d6d;font-weight:900;font-size:26px}
.foot-brand small{display:block;font-size:12px;font-weight:700;margin-top:4px}
.bottombar{left:0;top:2535px;width:1200px;height:32px;background:var(--red);color:var(--white);font-size:13px;text-align:center;line-height:32px}
</style>
</head>
<body>
<div class="page">

  <div class="abs topbar">
    <div class="abs phone">
      <svg width="20" height="20" viewBox="0 0 20 20"><circle cx="10" cy="10" r="9" fill="none" stroke="#fff" stroke-width="1.6"/><path d="M7 5l2 2-1 1.5c.7 1.5 1.8 2.6 3.3 3.3L12.8 11l2 2-1.3 1.5C9.5 14 6 10.5 5.6 6.4z" fill="#fff"/></svg>
      012-555-0148
    </div>
    <div class="abs login">
      <svg width="16" height="16" viewBox="0 0 16 16"><circle cx="8" cy="4.5" r="3.5" fill="#fff"/><path d="M1 16c0-4 3-6.5 7-6.5s7 2.5 7 6.5z" fill="#fff"/></svg>
      Telemetry Login
    </div>
  </div>

  <div class="abs brand"><span class="dot"></span>CORVANE</div>
  <nav class="abs nav">
    <a class="active" href="#">HOME</a>
    <a href="#">ABOUT US</a>
    <a href="#">PRODUCTS</a>
    <a href="#">TELEMETRY</a>
    <a href="#">CONTACT US</a>
  </nav>

  <section class="abs hero" role="img" aria-label="Black and white photograph of oil field workers at a wellhead">
    <span class="abs arrow" style="left:16px"></span>
    <span class="abs arrow" style="right:16px"></span>
    <div class="abs caption">We Use Innovative Methods And Tools In Its Quest To Produce Affordable Energy</div>
  </section>

  <section class="welcome">
    <h1 class="abs">Welcome To <span>CORVANE</span></h1>
    <div class="abs rule"></div>
    <p class="abs" style="top:737px">The dynamic nature of the Oil Industry requires smart and innovative methods and tools in its quest to produce affordable energy. Similarly, companies must seek cost-effectiveness and efficiency at every phase of production and distribution in order to stay competitive.</p>
    <p class="abs" style="top:829px">Corvane Systems, Inc., is here to offer its ample experience in designing and manufacturing automated solutions to the beam pump control. Besides its line of smart Pump-Off Controllers (POC) solutions include local wireless technology, telemetry SCADA and internet connectivity.</p>
  </section>

  <section class="abs benefits">
    <h2 class="abs">Your <span>Benefits</span></h2>
    <div class="abs rule"></div>
    <svg class="abs" style="left:0;top:0" width="1200" height="723">
      <g stroke="#b5b5b5" stroke-width="2" stroke-dasharray="3 5" fill="none">
        <line x1="610" y1="305" x2="321" y2="167"/>
        <line x1="610" y1="305" x2="877" y2="167"/>
        <line x1="610" y1="305" x2="349" y2="494"/>
        <line x1="610" y1="305" x2="603" y2="584"/>
        <line x1="610" y1="305" x2="864" y2="494"/>
      </g>
    </svg>
    <div class="abs hub"><span class="dot"></span>CORVANE</div>

    <div class="abs benefit" style="left:201px;top:107px">
      <div class="icon"><svg width="64" height="64" viewBox="0 0 64 64" fill="none" stroke="#222" stroke-width="4"><line x1="6" y1="18" x2="50" y2="10"/><path d="M50 6v16"/><path d="M28 14L18 56M28 14l10 42M14 56h28"/><path d="M54 22v34"/></svg></div>
      Increased Oil<br>Production
    </div>
    <div class="abs benefit" style="left:757px;top:107px">
      <div class="icon"><svg width="60" height="60" viewBox="0 0 60 60"><circle cx="30" cy="32" r="22" fill="none" stroke="#222" stroke-width="6"/><rect x="25" y="2" width="10" height="6" fill="#222"/><path d="M30 32V18" stroke="#222" stroke-width="5"/></svg></div>
      Quick ROI
    </div>
    <div class="abs benefit" style="left:229px;top:434px">
      <div class="icon"><svg width="56" height="56" viewBox="0 0 56 56" fill="none" stroke="#222" stroke-width="3.5" stroke-linejoin="round"><rect x="6" y="24" width="10" height="26"/><path d="M16 26l10-18c4 0 6 3 5 7l-2 8h16c3 0 5 3 4 6l-4 16c-1 3-3 5-6 5H16"/></svg></div>
      Ease Of Use
    </div>
    <div class="abs benefit" style="left:483px;top:524px">
      <div class="icon"><svg width="50" height="56" viewBox="0 0 50 56"><path d="M12 24V16a13 13 0 0 1 26 0v8" fill="none" stroke="#222" stroke-width="6"/><rect x="5" y="24" width="40" height="30" rx="3" fill="#222"/><rect x="22" y="33" width="6" height="12" fill="#fff"/></svg></div>
      Data Security
    </div>
    <div class="abs benefit" style="left:744px;top:434px">
      <div class="icon"><svg width="56" height="56" viewBox="0 0 56 56"><path d="M38 6a12 12 0 0 0-11 16L8 41a5 5 0 0 0 7 7l19-19A12 12 0 0 0 50 18l-7 7-8-2-2-8 7-7z" fill="#222"/></svg></div>
      Low Maintenance<br>Cost
    </div>
  </section>

  <section class="abs promo" role="img" aria-label="Blurred red photograph of oil field equipment">
    <div class="abs line" style="top:24px">Are your wells running under a Timer switch?</div>
    <div class="abs line" style="top:67px">Have you thought of increasing the barrel<br>count at each well?</div>
    <div class="abs line big" style="top:164px">Corvane CAN DO IT!(*) TRY IT!</div>
    <div class="abs badge">A True<br>Cellular<br>POC</div>
  </section>

  <section class="feedback">
    <h3 class="abs">CUSTOMER FEEDBACK</h3>
    <div class="abs rule"></div>
    <div class="abs quote">
      <span class="abs mark">“</span>
      Lorem ipsum dolor sit amet, consectetuer adipiscing elit, sed diam nonummy nibh euismod tincidunt ut laoreet re gan aliqam erat volutpat wisi enim ad minim veniam, quis nostrud exerci tation ullamcorper suscipit lobortis nisl ut aliquip modo consequatis autem vel eum iriure dolor in hendrerit in vulputate velit esse molestie consequat, vel illum dolore eu.
    </div>
    <div class="abs avatar" role="img" aria-label="Customer portrait"></div>
    <div class="abs author">Marek Dalton, Fieldline Energy , USA</div>
    <div class="abs dots"><i></i><i></i><i></i><i></i></div>
    <div class="abs clients">
      <span>HALVORA</span><span>BRINEX</span><span>kestra</span><span>Ravelle</span><span>Ostrin</span><span>Pellmark</span><span>Dunmore</span><span>Wrenfield</span>
    </div>
  </section>

  <footer class="abs footer">
    <h4 style="left:148px">Quick Links</h4>
    <div class="col-rule" style="left:148px;width:150px"></div>
    <ul class="links" style="left:152px;top:72px">
      <li>Home</li><li>About Us</li><li>Products</li><li>Telemetry</li><li>Contact Us</li>
    </ul>
    <h4 style="left:336px">Contact Details</h4>
    <div class="col-rule" style="left:336px;width:236px"></div>
    <ul class="contact" style="left:338px;top:74px">
      <li><svg width="12" height="16" viewBox="0 0 12 16"><path d="M6 0a6 6 0 0 0-6 6c0 4.5 6 10 6 10s6-5.5 6-10a6 6 0 0 0-6-6z" fill="#fff"/><circle cx="6" cy="6" r="2" fill="#2c2c2c"/></svg><span>418, Mesa Ridge Road,<br>Suite # 210<br>Kellan, Tx 79990</span></li>
      <li><svg width="14" height="14" viewBox="0 0 14 14"><path d="M2 1l3 3-1.5 2c1 2 2.5 3.5 4.5 4.5L10 9l3 3-2 2C5 13 1 9 0 3z" fill="#fff"/></svg>915.555.0172</li>
      <li><svg width="14" height="14" viewBox="0 0 14 14"><path d="M2 1l3 3-1.5 2c1 2 2.5 3.5 4.5 4.5L10 9l3 3-2 2C5 13 1 9 0 3z" fill="#fff"/></svg>432.555.0193</li>
      <li><svg width="14" height="12" viewBox="0 0 14 12"><rect width="14" height="12" fill="#fff"/><path d="M0 0l7 6 7-6" fill="none" stroke="#2c2c2c" stroke-width="1.5"/></svg>info@corvanesystems.example</li>
    </ul>
    <h4 style="left:642px">Location Map</h4>
    <div class="col-rule" style="left:642px;width:230px"></div>
  </footer>
  <div class="abs map" role="img" aria-label="Street map showing the office location"></div>
  <div class="abs maplink">View Location</div>
  <div class="abs foot-brand">CORVANE<small>PATENT 4402918</small></div>
  <div class="abs bottombar">© 2014 Corvane &nbsp;|&nbsp; All Rights Reserved.</div>

</div>
</body>
</html>
```